Willowmere Rites Studio creates individual, personalised ceremonies to celebrate weddings, naming days,coming of age, significant age, divorce and final resting rites. Ceremonies and meaningful rituals are created in collaboration with the individual to reflect their hopes and desires, how they will/have embrace/d their lives. The final design should have the logo (purple) on a white/silver background on the right hand side of the card. Name of business and contact details in red on a black background on the left
Updates

Hi All, have only just realised I have paid for a double sided card, yep, a newbie! Sorry to set the cat amongst the pigeons but could we put 'creating...... etc' on the back?

Target Market(s)

Couples marrying, renewing of vows, baby naming days, coming of age, significant age, divorce, funeral ceremonies. The target market predominantly will be couples marrying.

Industry/Entity Type

Business

Contact Information for Business Card

Willowmere Rites Studio, Corinna Thwaite, 0472-938025 willowmereritesstudio7@postvane.example
"Crafting tailored, heartfelt rituals for every chapter"

Font styles to use
Script

Colors
eb1f27
6b449b
f3f0f8

Requirements
Must have
• On initial entry, and now, the logo was not displayed in full - the bottom part was cut off - this needs to be in it's entirety. Colours as previously specified are non-negotiable. Font and placement of characters will be assessed as produced.
Should not have
• Telephone symbol, call us, director,grammatical symbols ( : )

```html
<!DOCTYPE html>
<html lang="en">
<head>
<meta charset="utf-8">
<title>Willowmere Rites Studio — Business Card</title>
<link rel="stylesheet" href="https://fonts.googleapis.com/css2?family=Noto+Serif:ital,wght@0,400;1,400&family=Questrial&display=swap">
<style>
  :root {
    --page: #ffffff;
    --ink-dark: #231f20;
    --pattern-tone: #3a3637;
    --brand-red: #eb1f27;
    --brand-purple: #6b449b;
    --silver: #f3f0f8;
    --white: #ffffff;
    --card-shadow: rgba(0, 0, 0, 0.18);
  }
  * { margin: 0; padding: 0; box-sizing: border-box; }
  html, body {
    width: 1200px;
    height: 784px;
    overflow: hidden;
    background: var(--page);
  }
  .canvas {
    position: relative;
    width: 1200px;
    height: 784px;
  }
  .business-card {
    position: absolute;
    left: 250px;
    top: 188px;
    width: 706px;
    height: 413px;
    display: flex;
    box-shadow: 0 1px 6px var(--card-shadow);
  }
  .contact-panel {
    position: relative;
    width: 474px;
    height: 100%;
    background: var(--ink-dark);
    overflow: hidden;
  }
  .contact-panel__pattern {
    position: absolute;
    inset: 0;
    background: radial-gradient(ellipse at 50% 45%, var(--pattern-tone) 0%, var(--ink-dark) 85%);
    opacity: 0.7;
  }
  .business-name {
    position: absolute;
    left: 28px;
    top: 36px;
    font-family: "Noto Serif", Georgia, serif;
    font-weight: 400;
    font-size: 29px;
    color: var(--brand-red);
    white-space: nowrap;
  }
  .contact-details {
    position: absolute;
    left: 30px;
    top: 284px;
    font-family: "Questrial", "Century Gothic", sans-serif;
    color: var(--white);
  }
  .contact-details__name {
    font-size: 26px;
    line-height: 36px;
    margin-bottom: 2px;
  }
  .contact-details__phone,
  .contact-details__email {
    font-size: 20px;
    line-height: 37px;
  }
  .brand-panel {
    position: relative;
    width: 232px;
    height: 100%;
    background: var(--silver);
    display: flex;
    flex-direction: column;
    align-items: center;
  }
  .brand-mark {
    margin-top: 64px;
    display: flex;
    flex-direction: column;
    align-items: center;
    gap: 14px;
  }
  .brand-mark__dot {
    width: 34px;
    height: 34px;
    border-radius: 50%;
    background: var(--brand-purple);
  }
  .brand-mark__name {
    font-family: "Noto Serif", Georgia, serif;
    font-weight: 400;
    font-size: 24px;
    line-height: 30px;
    color: var(--brand-purple);
    text-align: center;
  }
  .tagline {
    position: absolute;
    left: 0;
    right: 0;
    top: 318px;
    font-family: "Noto Serif", Georgia, serif;
    font-style: italic;
    font-size: 17px;
    line-height: 26px;
    color: var(--brand-purple);
    text-align: center;
  }
</style>
</head>
<body>
<main class="canvas">
  <article class="business-card">
    <section class="contact-panel">
      <div class="contact-panel__pattern" role="img" aria-label="Faint repeating ribbon-scroll pattern in dark grey"></div>
      <h1 class="business-name">Willowmere Rites Studio</h1>
      <div class="contact-details">
        <p class="contact-details__name">Corinna Thwaite</p>
        <p class="contact-details__phone">0472-938025</p>
        <p class="contact-details__email">willowmereritesstudio7@postvane.example</p>
      </div>
    </section>
    <section class="brand-panel">
      <div class="brand-mark">
        <span class="brand-mark__dot" aria-hidden="true"></span>
        <p class="brand-mark__name">Willowmere<br>Rites<br>Studio</p>
      </div>
      <p class="tagline">“Crafting tailored,<br>heartfelt rituals for<br>every chapter”</p>
    </section>
  </article>
</main>
</body>
</html>
```